We need a complete design for our construction company KELTO CONSTRUCTION based in Auckland New Zealand, we need a logo, website, business card, vehicle design etc..
We are a mid to high-end construction company who work mostly on residential projects and some commercial.

What we want to see in the design;
Professional,
Architectural,
Simple,
Alternative,

We want the design to communicate professionalism, high quality wormanship and and quality service.

Target Market(s)

People looking for a quality building/ construction company

Industry/Entity Type

Construction Company

Contact Information for Business Card

KELTO CONSTRUCTION.co.nz
Lino Verasek
lino@keltoconstruction.example.nz
021 5807 462

Logo Text

KELTO CONSTRUCTION

Number of Pages Required

5+ page

Font styles to use
Sans Serif

Colors

Designer to choose colors to be used in the design.

Requirements
Must have
• Must appear high end, professional, quality, be simple, easy to use, give security to potential clients
Nice to have
• high-quality photos of our recent projects
• about us page
• blog page
• contact us page
• high quality content
Should not have
• should not be hard to use and have too much going on.

```html
<!DOCTYPE html>
<html lang="en">
<head>
<meta charset="utf-8">
<title>Kelto Construction</title>
<link href="https://fonts.googleapis.com/css2?family=Montserrat:wght@500;600;700;800&family=Open+Sans:ital,wght@0,400;0,600;0,700;1,400&display=swap" rel="stylesheet">
<style>
:root{
  --navy:#1f2a4b;
  --navy-deep:#18213b;
  --orange:#f2a11b;
  --orange-dark:#d98c0c;
  --ink:#222a3a;
  --text:#6f7480;
  --light:#f3f3f4;
  --line:#e2e3e6;
  --white:#fff;
}
*{margin:0;padding:0;box-sizing:border-box}
html,body{width:1200px;height:4206px;overflow:hidden}
body{font-family:"Open Sans",Arial,sans-serif;color:var(--text);background:var(--white);position:relative}
.abs{position:absolute}
h1,h2,h3,h4,.head{font-family:"Montserrat",Arial,sans-serif;color:var(--ink)}
/* top bar */
.topbar{left:0;top:0;width:1200px;height:39px;background:var(--navy);color:#cfd4e2;font-size:12.5px}
.topbar .info{left:100px;top:0;height:39px;display:flex;align-items:center;gap:34px}
.topbar .info span{display:flex;align-items:center;gap:7px}
.topbar .cta{left:932px;top:0;width:168px;height:39px;background:var(--orange);color:var(--navy);font:700 12px "Montserrat",sans-serif;display:flex;align-items:center;justify-content:center}
/* header */
.header{left:0;top:39px;width:1200px;height:121px;background:#fff}
.brand{left:98px;top:25px;display:flex;align-items:center;gap:10px}
.brand .mark{width:26px;height:26px;background:var(--orange)}
.brand .name{font:800 18px "Montserrat",sans-serif;color:var(--navy);letter-spacing:.5px;line-height:1.1}
.nav{left:513px;top:43px;display:flex;gap:0;font:600 15px "Montserrat",sans-serif;color:var(--ink)}
.nav a{color:inherit;text-decoration:none;margin-right:42px;padding-bottom:8px}
.nav a.active{border-bottom:2px solid var(--orange)}
.search{left:1082px;top:45px}
/* hero */
.hero{left:0;top:160px;width:1200px;height:592px;background:linear-gradient(180deg,#142040 0%,#1f3466 38%,#3b3a44 62%,#8a5a2c 80%,#3a2c22 100%)}
.hero h1{position:absolute;left:0;width:1200px;top:178px;text-align:center;color:#fff;font-size:50px;font-weight:700;letter-spacing:1px}
.hero p{position:absolute;left:250px;width:700px;top:258px;text-align:center;color:#fff;font:600 21px/1.45 "Open Sans",sans-serif}
.btn{display:flex;align-items:center;justify-content:center;gap:8px;border-radius:30px;font:700 14px "Montserrat",sans-serif;color:#fff;background:var(--orange)}
.hero .btn{position:absolute;left:512px;top:356px;width:176px;height:46px}
.arrow{position:absolute;top:290px}
/* about */
.about h2{left:98px;top:835px;font-size:31px;font-weight:700}
.about p{width:490px;font-size:13.5px;line-height:1.7;left:98px}
.about .btn{left:98px;top:1100px;width:152px;height:43px}
.video{left:638px;top:845px;width:462px;height:300px;background:linear-gradient(160deg,#8fb3d6 0%,#c9d9e8 45%,#8b8f94 75%,#5b5f66 100%);border:6px solid #fff;box-shadow:0 0 0 1px var(--line)}
.play{left:843px;top:973px}
/* what we do */
.services{left:0;top:1228px;width:1200px;height:477px;background:linear-gradient(180deg,#f7f7f7,#ececee)}
.section-title{position:absolute;left:0;width:1200px;text-align:center;font:700 30px "Montserrat",sans-serif;color:var(--ink);letter-spacing:.5px}
.service{position:absolute;top:150px;width:300px;text-align:center}
.service .icon{width:114px;height:114px;border-radius:50%;margin:0 auto;border:5px solid #fff;box-shadow:0 0 0 2px var(--line);display:flex;align-items:center;justify-content:center}
.service h3{margin-top:32px;font-size:18px;font-weight:700}
.service p{margin-top:14px;font-size:12.5px;line-height:1.6}
/* split */
.split{top:1705px;width:600px;height:353px;color:#fff;text-align:center}
.split h2{color:#fff;font-size:34px;font-weight:700;margin-top:70px;letter-spacing:1px}
.split p{width:420px;margin:18px auto 0;font-size:13px;line-height:1.7;color:#f1f1f1}
.split .ghost{width:146px;height:38px;margin:22px auto 0;border:2px solid #fff;border-radius:22px;display:flex;align-items:center;justify-content:center;font:700 13px "Montserrat",sans-serif}
.res{left:0;background:linear-gradient(160deg,rgba(31,42,75,.93),rgba(31,42,75,.85)),linear-gradient(#4a5a6e,#2a3447)}
.com{left:600px;background:linear-gradient(160deg,rgba(236,160,28,.93),rgba(218,140,12,.9))}
/* projects */
.filters{left:0;width:1200px;top:2225px;display:flex;justify-content:center;gap:38px;font:600 13px "Montserrat",sans-serif;color:var(--ink)}
.filters .on{color:var(--orange);border-bottom:1px solid var(--orange)}
.tile{position:absolute}
.tile.big{background:linear-gradient(rgba(241,164,30,.86),rgba(241,164,30,.86)),#b98b4a;display:flex;flex-direction:column;align-items:center;justify-content:center;color:#fff;text-align:center}
.tile.big .btns{display:flex;gap:14px}
.tile.big .btns span{width:34px;height:34px;border-radius:50%;background:var(--navy);display:flex;align-items:center;justify-content:center}
.tile.big h4{color:#fff;font-size:18px;margin-top:16px}
.tile.big p{font-size:12.5px;line-height:1.6;width:320px;margin-top:10px}
/* testimonial */
.testimonial{left:0;top:2894px;width:1200px;height:359px;background:linear-gradient(90deg,#c88a22 0%,#2c3a62 30%,#1f2a4b 100%)}
.avatar{left:145px;top:99px;width:176px;height:176px;border-radius:50%;background:linear-gradient(160deg,#d9a88a,#6b4535);border:6px solid #fff}
.quote-badge{left:215px;top:262px;width:36px;height:36px;border-radius:50%;background:var(--orange);border:3px solid #fff}
.testimonial h2{left:385px;top:100px;color:#fff;font-size:30px;font-weight:700}
.testimonial p{left:385px;top:150px;width:690px;color:#e6e8ee;font-style:italic;font-size:14px;line-height:1.75}
.testimonial .who{left:385px;top:263px;color:#fff;font:700 14px "Montserrat",sans-serif}
.testimonial .who small{font:400 12px "Open Sans",sans-serif;color:#d7dbe5}
.circle-btn{width:32px;height:32px;border-radius:50%;background:#fff;display:flex;align-items:center;justify-content:center}
/* why / news */
.col-title{font:700 30px "Montserrat",sans-serif;color:var(--ink);border-bottom:3px solid var(--orange);padding-bottom:4px}
.acc{left:98px;width:510px}
.acc-row{height:42px;border:1px solid var(--line);display:flex;align-items:center;justify-content:space-between;padding-left:18px;font:600 14px "Montserrat",sans-serif;color:var(--ink);margin-bottom:5px}
.acc-row .plus{width:42px;height:42px;margin-right:-1px;background:var(--orange);color:#fff;display:flex;align-items:center;justify-content:center;font-size:20px}
.acc-row.open{background:var(--navy);color:#fff;margin-bottom:0}
.acc-body{border:1px solid var(--line);border-top:0;padding:22px 24px;font-size:12.5px;line-height:1.65;height:110px;margin-bottom:9px}
.news{left:670px;width:430px}
.news-item{display:flex;gap:18px;height:103px}
.thumb{width:118px;height:86px;flex:none}
.news-item h4{font:600 15.5px/1.45 "Open Sans",sans-serif;color:var(--navy)}
.meta{margin-top:10px;font-size:11px;color:var(--text);display:flex;gap:10px}
.meta i{display:inline-block;width:9px;height:9px;border-radius:50%;background:var(--orange);margin-right:4px;font-style:normal}
/* footer */
.footer{left:0;top:3808px;width:1200px;height:398px;background:var(--navy-deep);border-top:4px solid var(--orange);color:#c5cbda;font-size:12.5px}
.footer h4{color:#fff;font:700 14px "Montserrat",sans-serif}
.flinks li{list-style:none;margin-top:15px;display:flex;gap:9px;align-items:center}
.flinks li:before{content:"";border-left:5px solid var(--orange);border-top:4px solid transparent;border-bottom:4px solid transparent}
.contact-row{display:flex;gap:14px;margin-top:18px;line-height:1.5}
.email-box{width:248px;height:36px;border:1px solid #8892ab;padding:9px 10px;color:#c5cbda;margin-top:14px}
.sub-btn{width:94px;height:28px;margin-top:14px;font-size:11px}
.f-brand{left:880px;top:72px;width:220px;text-align:center}
.f-brand .mark{width:40px;height:40px;background:var(--orange);margin:0 auto 14px}
.f-brand .name{font:800 17px "Montserrat",sans-serif;color:#fff;letter-spacing:.5px}
.copy{left:98px;top:300px;width:1002px;border-top:1px solid #3a4466;padding-top:26px;display:flex;justify-content:space-between;align-items:center}
.social{display:flex;gap:12px}
.social span{width:38px;height:38px;border-radius:50%;border:2px solid #c5cbda}
</style>
</head>
<body>

<!-- top bar -->
<div class="abs topbar">
  <div class="abs info">
    <span><svg width="12" height="12" viewBox="0 0 24 24"><path fill="#f2a11b" d="M6.6 10.8a15 15 0 0 0 6.6 6.6l2.2-2.2c.3-.3.7-.4 1-.2 1.1.4 2.3.6 3.6.6.6 0 1 .4 1 1V20c0 .6-.4 1-1 1A17 17 0 0 1 3 4c0-.6.4-1 1-1h3.5c.6 0 1 .4 1 1 0 1.3.2 2.5.6 3.6.1.3 0 .7-.2 1z"/></svg>(+64) 9 555 0142</span>
    <span><svg width="12" height="12" viewBox="0 0 24 24"><circle cx="12" cy="12" r="9" fill="none" stroke="#f2a11b" stroke-width="2.5"/><path d="M12 7v5l3 2" stroke="#f2a11b" stroke-width="2.5" fill="none"/></svg>Mon - Sat: 9:00 - 18:00</span>
    <span><svg width="13" height="11" viewBox="0 0 24 18"><rect x="1" y="1" width="22" height="16" fill="none" stroke="#f2a11b" stroke-width="2.5"/><path d="M1 1l11 9 11-9" fill="none" stroke="#f2a11b" stroke-width="2.5"/></svg>info@keltoconstruction.example.nz</span>
  </div>
  <div class="abs cta">GET A CONSULTATION</div>
</div>

<!-- header -->
<header class="abs header">
  <div class="abs brand"><div class="mark"></div><div class="name">KELTO<br>CONSTRUCTION</div></div>
  <nav class="abs nav"><a class="active">HOME</a><a>ABOUT US</a><a>PROJECTS</a><a>BLOG</a><a>CONTACT US</a></nav>
  <svg class="abs search" width="18" height="18" viewBox="0 0 24 24"><circle cx="10" cy="10" r="7" fill="none" stroke="#222a3a" stroke-width="3"/><path d="M15 15l7 7" stroke="#222a3a" stroke-width="3"/></svg>
</header>

<!-- hero -->
<section class="abs hero" role="img" aria-label="Night city skyline with a tower and light trails along curving motorways">
  <h1>KELTO CONSTRUCTION</h1>
  <p>Neque porro quisquam estui dolorem ipsum quia dolor sit amet, consectetur adipisci velit sed quia non numquam</p>
  <div class="btn">READ MORE <svg width="13" height="13" viewBox="0 0 24 24"><circle cx="12" cy="12" r="11" fill="#fff"/><path d="M10 7l5 5-5 5" stroke="#f2a11b" stroke-width="3" fill="none"/></svg></div>
  <svg class="arrow" style="left:36px" width="14" height="22" viewBox="0 0 14 22"><path d="M12 2L3 11l9 9" stroke="#fff" stroke-width="3" fill="none"/></svg>
  <svg class="arrow" style="left:1150px" width="14" height="22" viewBox="0 0 14 22"><path d="M2 2l9 9-9 9" stroke="#fff" stroke-width="3" fill="none"/></svg>
</section>

<!-- about -->
<section class="about">
  <h2 class="abs">ABOUT KELTO CONSTRUCTION</h2>
  <p class="abs" style="top:900px">At vero eos et accusamus et iusto odio dignissimos ducimus qui blanditiis praesentium voluptatum deleniti atque corrupti quos.</p>
  <p class="abs" style="top:968px">Nam libero tempore, cum soluta nobis est eligendi optio cumque nihil impedit quo minus id quod maxime placeat facere possimus, omnis voluptas assumenda est, omnis dolor repellendus. Temporibus autem quibusdam et aut officiis debitis aut rerum necessitatibus saepe eveniet ut et voluptates repudiandae.</p>
  <div class="abs btn">READ MORE <svg width="13" height="13" viewBox="0 0 24 24"><circle cx="12" cy="12" r="11" fill="#fff"/><path d="M10 7l5 5-5 5" stroke="#f2a11b" stroke-width="3" fill="none"/></svg></div>
  <div class="abs video" role="img" aria-label="Two engineers in hard hats reviewing plans beside a tower crane"></div>
  <svg class="abs play" width="52" height="52" viewBox="0 0 52 52"><circle cx="26" cy="26" r="25" fill="#d4202a"/><path d="M21 16l14 10-14 10z" fill="#fff"/></svg>
</section>

<!-- services -->
<section class="abs services" aria-label="What we do">
  <h2 class="section-title" style="top:60px">WHAT WE DO</h2>
  <div class="service" style="left:96px">
    <div class="icon" style="background:var(--orange)"><svg width="50" height="50" viewBox="0 0 50 50"><rect x="10" y="14" width="30" height="24" fill="none" stroke="#fff" stroke-width="3"/><path d="M10 14l15-8 15 8M18 38V26h14v12" fill="none" stroke="#fff" stroke-width="3"/></svg></div>
    <h3>CONSTRUCTION</h3>
    <p>Nam libero tempore, cum soluta nobis eligendi cumque nihil impedit minus id quod maxime placeat facere possimus, omnis volup assumenda</p>
  </div>
  <div class="service" style="left:450px">
    <div class="icon" style="background:var(--navy)"><svg width="50" height="50" viewBox="0 0 50 50"><path d="M25 6L12 40h26z" fill="none" stroke="#fff" stroke-width="3"/><path d="M8 44h34M19 26h12" stroke="#f2a11b" stroke-width="3"/></svg></div>
    <h3>ENGINEERING</h3>
    <p>Nam libero tempore, cum soluta nobis eligendi cumque nihil impedit minus id quod maxime placeat facere possimus, omnis volup assumenda</p>
  </div>
  <div class="service" style="left:804px">
    <div class="icon" style="background:var(--orange)"><svg width="50" height="50" viewBox="0 0 50 50"><path d="M10 26a15 15 0 0 1 30 0z" fill="#fff"/><rect x="8" y="26" width="34" height="4" fill="#fff"/><circle cx="25" cy="37" r="7" fill="none" stroke="#fff" stroke-width="3"/></svg></div>
    <h3>PROJECT MANAGEMENT</h3>
    <p>Nam libero tempore, cum soluta nobis eligendi cumque nihil impedit minus id quod maxime placeat facere possimus, omnis volup assumenda</p>
  </div>
</section>

<!-- residential / commercial -->
<section class="abs split res" role="img" aria-label="Residential home exterior behind navy overlay">
  <h2>RESIDENTIAL</h2>
  <p>Nemo enim ipsam voluptatem quia voluptas sit aspernatur aut odit fugit, sed quia consequuntur magni dolores eos qui ratione voluptatem sequi nesciunt porro quisquam</p>
  <div class="ghost">GET A QUOTE</div>
</section>
<section class="abs split com" role="img" aria-label="Commercial building facade behind amber overlay">
  <h2>COMMERCIAL</h2>
  <p>Nemo enim ipsam voluptatem quia voluptas sit aspernatur aut odit fugit, sed quia consequuntur magni dolores eos qui ratione voluptatem sequi nesciunt porro quisquam</p>
  <div class="ghost">GET A QUOTE</div>
</section>

<!-- projects -->
<h2 class="section-title" style="top:2140px">LATEST PROJECTS</h2>
<div class="abs filters"><span class="on">ALL PROJECTS</span><span>INTERIOR DESIGN</span><span>RESIDENTIAL</span><span>COMMERCIAL</span></div>
<div class="tile" style="left:98px;top:2288px;width:258px;height:160px;background:linear-gradient(180deg,#9cc3e6,#6d7f63 70%,#4b6a3a)" role="img" aria-label="Two-storey green family house"></div>
<div class="tile big" style="left:372px;top:2288px;width:456px;height:337px" role="img" aria-label="Featured residential project house">
  <div class="btns"><span><svg width="14" height="14" viewBox="0 0 24 24"><circle cx="10" cy="10" r="6" fill="none" stroke="#fff" stroke-width="3"/><path d="M14 14l6 6" stroke="#fff" stroke-width="3"/></svg></span><span><svg width="14" height="14" viewBox="0 0 24 24"><circle cx="12" cy="12" r="10" fill="#fff"/><path d="M12 10v7M12 6v1" stroke="#1f2a4b" stroke-width="3"/></svg></span></div>
  <h4>RESIDENTIAL PROJECTS</h4>
  <p>Nequeporro quisquam voluptatem quia voluptas sit aspernatur aut odit aut fugit, sed quia consequuntur</p>
</div>
<div class="tile" style="left:842px;top:2288px;width:258px;height:160px;background:linear-gradient(180deg,#e9edf0,#c4c9cd 60%,#9ea4a8)" role="img" aria-label="Empty bright commercial interior"></div>
<div class="tile" style="left:98px;top:2465px;width:258px;height:160px;background:linear-gradient(180deg,#a9c8e4,#e1d9cb 55%,#5f7a47)" role="img" aria-label="White suburban house with lawn"></div>
<div class="tile" style="left:842px;top:2465px;width:258px;height:160px;background:linear-gradient(180deg,#6ea3d8,#b58a60 55%,#4f7d3a)" role="img" aria-label="Modern apartment block"></div>
<div class="tile" style="left:98px;top:2640px;width:258px;height:160px;background:linear-gradient(160deg,#3b2416,#8b4f2b 55%,#c78c55)" role="img" aria-label="Timber kitchen interior"></div>
<div class="tile" style="left:372px;top:2640px;width:258px;height:160px;background:linear-gradient(180deg,#c9d6e2,#7b6e60 50%,#4e6a35)" role="img" aria-label="Modern house with flat roof"></div>
<div class="tile" style="left:642px;top:2640px;width:458px;height:160px;background:linear-gradient(160deg,#f1e6d6,#c89a6b 55%,#7a4a2a)" role="img" aria-label="Warm living room interior"></div>

<!-- testimonial -->
<section class="abs testimonial" role="img" aria-label="Houses in background behind navy and amber overlay">
  <div class="abs avatar" role="img" aria-label="Client portrait"></div>
  <div class="abs quote-badge"></div>
  <h2 class="abs">WHAT OUR CLIENTS SAY</h2>
  <p class="abs">Nor again is there anyone who loves or pursues or desires to obtain pain of itself, because it is pain but because occasionally circumstances occur in which toil and pain can procure him some great pleasure. To take a trivial example, which of us ever undertakes laborious physical exercise</p>
  <div class="abs who">MARA TENNANT, <small>Creative Manager</small></div>
  <div class="abs circle-btn" style="left:14px;top:198px"><svg width="10" height="12" viewBox="0 0 10 12"><path d="M8 1L2 6l6 5" stroke="#1f2a4b" stroke-width="2" fill="none"/></svg></div>
  <div class="abs circle-btn" style="left:1130px;top:198px"><svg width="10" height="12" viewBox="0 0 10 12"><path d="M2 1l6 5-6 5" stroke="#1f2a4b" stroke-width="2" fill="none"/></svg></div>
</section>

<!-- why choose -->
<h2 class="abs col-title" style="left:98px;top:3330px">WHY CHOOSE US?</h2>
<div class="abs acc" style="top:3410px">
  <div class="acc-row open"><span>&#9632;&nbsp; We Are Creative</span><span class="plus">&minus;</span></div>
  <div class="acc-body">Nemo enim ipsam voluptatem quia voluptas sit aspernatur aut odit aut fugit, sed quia consequuntur magni dolores eos qui ratione voluptatem at sequi nesciunt. Neque porro quisquam est, qui dolorem</div>
  <div class="acc-row"><span>&#9679;&nbsp; Honest And Dependable</span><span class="plus">+</span></div>
  <div class="acc-row"><span>&#10003;&nbsp; Quality Commitment</span><span class="plus">+</span></div>
  <div class="acc-row"><span>&#9650;&nbsp; We Are Always Improving</span><span class="plus">+</span></div>
</div>

<!-- news -->
<h2 class="abs col-title" style="left:670px;top:3330px">LATEST NEWS</h2>
<div class="abs news" style="top:3410px">
  <div class="news-item"><div class="thumb" style="background:linear-gradient(160deg,#d9c2a3,#8a6644)" role="img" aria-label="Interior renovation"></div><div><h4>Neque porro quisquam quied dolorem ipsum quia dolor sit amet.</h4><div class="meta"><span><i></i>By Alden,</span><span><i></i>18/03/18,</span><span><i></i>35 Comments</span></div></div></div>
  <div class="news-item"><div class="thumb" style="background:linear-gradient(180deg,#7fb0dc,#6b6f78)" role="img" aria-label="High-rise under construction"></div><div><h4>Neque porro quisquam quied dolorem ipsum quia dolor sit amet.</h4><div class="meta"><span><i></i>By Alden,</span><span><i></i>18/03/18,</span><span><i></i>35 Comments</span></div></div></div>
  <div class="news-item"><div class="thumb" style="background:linear-gradient(180deg,#c9d2db,#7d6a58)" role="img" aria-label="Building frame at site"></div><div><h4>Neque porro quisquam quied dolorem ipsum quia dolor sit amet.</h4><div class="meta"><span><i></i>By Alden,</span><span><i></i>18/03/18,</span><span><i></i>35 Comments</span></div></div></div>
</div>

<!-- footer -->
<footer class="abs footer">
  <div class="abs" style="left:98px;top:72px">
    <h4>QUICK LINKS</h4>
    <ul class="flinks"><li>Home</li><li>About us</li><li>Projects</li><li>Blog</li><li>Contact Us</li></ul>
  </div>
  <div class="abs" style="left:290px;top:72px;width:230px">
    <h4>CONTACT US</h4>
    <div class="contact-row"><svg width="12" height="16" viewBox="0 0 12 16"><path d="M6 0a6 6 0 0 0-6 6c0 4.5 6 10 6 10s6-5.5 6-10a6 6 0 0 0-6-6z" fill="#fff"/><circle cx="6" cy="6" r="2" fill="#18213b"/></svg><span>48 Harbour Lane, Parnell<br>AKL 1052</span></div>
    <div class="contact-row"><svg width="13" height="13" viewBox="0 0 24 24"><path fill="#fff" d="M6.6 10.8a15 15 0 0 0 6.6 6.6l2.2-2.2c.3-.3.7-.4 1-.2 1.1.4 2.3.6 3.6.6.6 0 1 .4 1 1V20c0 .6-.4 1-1 1A17 17 0 0 1 3 4c0-.6.4-1 1-1h3.5c.6 0 1 .4 1 1 0 1.3.2 2.5.6 3.6.1.3 0 .7-.2 1z"/></svg><span>(+64) 9 555 0187</span></div>
    <div class="contact-row"><svg width="14" height="11" viewBox="0 0 24 18"><rect x="0" y="0" width="24" height="18" fill="#fff"/><path d="M1 1l11 9 11-9" fill="none" stroke="#18213b" stroke-width="2"/></svg><span>info@keltoconstruction.example.nz</span></div>
  </div>
  <div class="abs" style="left:558px;top:72px;width:260px">
    <h4>NEWSLETTER SUBSCRIPTION</h4>
    <p style="margin-top:16px;line-height:1.5">Register your Email Address to get information about us</p>
    <div class="email-box">Email Address</div>
    <div class="btn sub-btn">SUBSCRIBE</div>
  </div>
  <div class="abs f-brand"><div class="mark"></div><div class="name">KELTO CONSTRUCTION</div></div>
  <div class="abs copy">
    <span>Copyrights &copy; 2018 Kelto Construction. All Rights Reserved.</span>
    <div class="social"><span></span><span></span><span></span><span></span></div>
  </div>
</footer>

</body>
</html>
```